Business Card Design Can you design a business card design? Looking for something unique and differe

Can you design a business card design? Looking for something unique and different. Can you design a business card design? Looking for something unique and different.Can you design a business card design? Looking for something unique and different.Can you design a business card design? Looking for something unique and different.Can you design a business card design? Looking for something unique and different.Can you design a business card design? Looking for something unique and different.

Industry/Entity Type

Business

Contact Information for Business Card

Can you design a business card design? Looking for something unique and different.

Font styles to use
Serif

```html
<!DOCTYPE html>
<html lang="en">
<head>
<meta charset="utf-8">
<title>Meridian Business Card</title>
<link rel="stylesheet" href="https://fonts.googleapis.com/css2?family=Source+Sans+3:wght@400;600&display=swap">
<style>
  :root {
    --backdrop: #3b3430;
    --card: #1c1b1d;
    --violet: #8c6aa6;
    --violet-soft: #a585bd;
    --white: #f1eff2;
    --grey: #bdb6b9;
    --divider: #4a474c;
  }
  * { box-sizing: border-box; margin: 0; padding: 0; }
  html, body { width: 1200px; height: 844px; overflow: hidden; }
  body {
    background: var(--backdrop);
    font-family: "Source Sans 3", sans-serif;
    position: relative;
  }
  .card {
    position: absolute;
    top: 272px;
    width: 525px;
    height: 300px;
    background: var(--card);
    border-radius: 4px;
    box-shadow: 0 12px 30px rgba(0,0,0,.45);
  }
  .card--front { left: 55px; }
  .card--back { left: 620px; display: flex; align-items: center; justify-content: center; }

  .brand {
    position: absolute;
    left: 0; right: 0; top: 52px;
    display: flex; align-items: center; justify-content: center; gap: 10px;
    color: var(--violet);
    font-weight: 600;
    font-size: 36px;
    letter-spacing: .5px;
  }
  .brand__mark { width: 14px; height: 14px; background: var(--violet); }

  .identity {
    position: absolute;
    right: 280px; top: 150px;
    text-align: right;
    white-space: nowrap;
  }
  .identity__name { color: var(--white); font-weight: 600; font-size: 21px; line-height: 1.1; }
  .identity__role { color: var(--violet-soft); font-size: 15px; margin-bottom: 12px; }
  .identity__address { color: var(--white); font-size: 15px; line-height: 1.2; }

  .divider {
    position: absolute;
    left: 262px; top: 148px;
    width: 1px; height: 110px;
    background: var(--divider);
  }

  .contacts {
    position: absolute;
    left: 280px; top: 150px;
    list-style: none;
  }
  .contacts li {
    display: flex; align-items: center; gap: 9px;
    color: var(--white);
    font-size: 15px;
    height: 24px;
    white-space: nowrap;
  }
  .contacts svg { width: 15px; height: 15px; flex: none; }

  .back-brand {
    display: flex; align-items: center; gap: 16px;
    color: var(--grey);
    font-weight: 600;
    font-size: 54px;
  }
  .back-brand__mark { width: 22px; height: 22px; background: var(--grey); }
</style>
</head>
<body>
  <section class="card card--front">
    <div class="brand"><span class="brand__mark"></span>Meridian</div>

    <div class="identity">
      <p class="identity__name">Daniel Hart</p>
      <p class="identity__role">Managing Director</p>
      <p class="identity__address">48 Harbour Lane, Suite 210<br>Westbridge, 20417</p>
    </div>

    <div class="divider"></div>

    <ul class="contacts">
      <li>
        <svg viewBox="0 0 16 16"><rect width="16" height="16" rx="2" fill="var(--violet)"/><path d="M4 6c0-1 1-2 4-2s4 1 4 2v1H10V6H6v1H4z M5 8h6l1 4H4z" fill="var(--white)"/></svg>
        (021)-555-0148
      </li>
      <li>
        <svg viewBox="0 0 16 16"><rect width="16" height="16" rx="2" fill="var(--violet)"/><rect x="5.5" y="3" width="5" height="10" rx="1" fill="var(--white)"/></svg>
        555-019-2364
      </li>
      <li>
        <svg viewBox="0 0 16 16"><rect width="16" height="16" rx="2" fill="var(--violet)"/><rect x="3.5" y="5" width="9" height="6" fill="var(--white)"/><path d="M3.5 5l4.5 3.5 4.5-3.5" fill="none" stroke="var(--violet)"/></svg>
        hello@meridian.co
      </li>
      <li>
        <svg viewBox="0 0 16 16"><rect width="16" height="16" rx="2" fill="var(--violet)"/><path d="M5 11l6-6" stroke="var(--white)" stroke-width="1.6"/><rect x="3.5" y="9" width="3.5" height="3.5" rx="1.5" fill="none" stroke="var(--white)"/><rect x="9" y="3.5" width="3.5" height="3.5" rx="1.5" fill="none" stroke="var(--white)"/></svg>
        www.meridian.co
      </li>
    </ul>
  </section>

  <section class="card card--back">
    <div class="back-brand"><span class="back-brand__mark"></span>Meridian</div>
  </section>
</body>
</html>
```